Web App Design Project

Need to provide graphical design of 2 web pages according to attached wireframes.

Colors should be adjusted for the 65+ population meaning not too bright.

App logo should be created as well - logo should represent long and good life.

Target Market(s)

65 years old and above

```html
<!DOCTYPE html>
<html lang="en">
<head>
<meta charset="utf-8">
<title>Home Measurements</title>
<link href="https://fonts.googleapis.com/css2?family=Open+Sans:wght@400;600;700&display=swap" rel="stylesheet">
<style>
  :root{
    --page:#ebeced;
    --header-top:#63c5f4;
    --header-bottom:#3b93d3;
    --blue:#3a96d2;
    --panel-grey:#ededed;
    --sidebar:#ececec;
    --white:#ffffff;
    --line:#c9cbd6;
    --row-line:#b8bbcb;
    --text-grey:#7c7f8c;
    --text-dark:#5d606c;
    --value:#f26a3a;
    --info:#2aa58a;
    --nav-bg:#f3f3f3;
    --nav-line:#b4b4b4;
    --green:#6ab64c;
    --orange-top:#f7703c;
    --orange-bottom:#e8452a;
    --purple:#7a4fb0;
    --amber:#f5a638;
    --teal:#2f9d86;
    --red:#dc5248;
    --button-grey:#8e919c;
  }
  *{box-sizing:border-box;margin:0;padding:0}
  html,body{width:1200px;height:900px;overflow:hidden}
  body{background:var(--page);font-family:"Open Sans",Arial,sans-serif;position:relative}
  .app{position:absolute;left:100px;top:120px;width:1000px;height:660px;background:var(--white);box-shadow:0 10px 40px rgba(0,0,0,.25);overflow:hidden}
  .app-header{position:absolute;left:0;top:0;width:1000px;height:60px;background:linear-gradient(var(--header-top),var(--header-bottom));color:var(--white)}
  .brand{position:absolute;left:0;top:0;width:200px;height:60px;border-right:1px solid rgba(255,255,255,.35)}
  .brand-dot{position:absolute;left:20px;top:14px;width:32px;height:32px;border-radius:50%;background:rgba(255,255,255,.85)}
  .brand-name{position:absolute;left:73px;top:12px;font-size:18px;font-weight:700;line-height:22px}
  .brand-slogan{position:absolute;left:73px;top:34px;font-size:9px;font-weight:600;line-height:12px}
  .welcome{position:absolute;left:215px;top:19px;font-size:15px;color:#e8f5fd}
  .welcome strong{color:var(--white);font-weight:700}
  .text-size{position:absolute;left:610px;top:14px;display:flex;align-items:baseline;gap:12px;color:var(--white)}
  .text-size span:nth-child(1){font-size:11px;opacity:.8}
  .text-size span:nth-child(2){font-size:17px;font-weight:700}
  .text-size span:nth-child(3){font-size:20px;opacity:.8}
  .search{position:absolute;left:686px;top:14px;width:163px;height:31px;border:1px solid rgba(255,255,255,.45);background:rgba(255,255,255,.12);font-size:14px;color:#dbeffc;padding:7px 8px}
  .search svg{position:absolute;right:8px;top:7px}
  .header-btn{position:absolute;top:14px;height:31px;border-radius:2px;background:linear-gradient(#56b5ea,#3585c9);box-shadow:0 1px 2px rgba(0,0,0,.25);font-size:16px;font-weight:700;text-align:center;line-height:31px}
  .btn-help{left:888px;width:32px}
  .btn-exit{left:934px;width:52px}
  .sidebar{position:absolute;left:0;top:60px;width:200px;height:470px;background:var(--sidebar);border-right:1px solid #dcdcdc}
  .sidebar-title{position:absolute;left:16px;top:24px;font-size:17px;font-weight:600;color:var(--blue)}
  .tab{position:absolute;left:10px;width:190px;height:90px;display:flex;align-items:center;gap:12px;font-size:15px;font-weight:600;color:var(--text-grey)}
  .tab-active{top:70px;background:var(--white);color:var(--text-dark);padding-left:35px}
  .tab-pressure{top:170px;padding-left:30px}
  .toolbar{position:absolute;left:200px;top:60px;width:800px;height:70px;background:var(--panel-grey)}
  .add-measure{position:absolute;left:30px;top:22px;display:flex;align-items:center;gap:8px;font-size:15px;font-weight:600;color:var(--blue)}
  .settings{position:absolute;right:30px;top:22px}
  .entry{position:absolute;left:229px;width:742px;height:62px;border:1px solid var(--row-line);border-radius:3px;background:var(--white)}
  .entry-1{top:160px}
  .entry-2{top:252px}
  .entry-date{position:absolute;left:14px;top:21px;font-size:15px;font-weight:600;color:var(--blue)}
  .entry-note{position:absolute;left:147px;top:21px;font-size:15px;color:var(--text-grey)}
  .comment-btn{position:absolute;left:147px;top:15px;height:30px;padding:0 8px;background:var(--button-grey);color:var(--white);font-size:13px;font-weight:700;line-height:30px;border-radius:2px}
  .entry-value{position:absolute;left:576px;top:21px;font-size:15px;font-weight:700;color:var(--value)}
  .entry-info{position:absolute;left:700px;top:20px}
  .bottom-nav{position:absolute;left:0;top:530px;width:1000px;height:130px;background:var(--nav-bg);border-top:3px solid var(--nav-line);display:grid;grid-template-columns:144px 141px 143px 143px 143px 143px 143px}
  .nav-item{position:relative;height:127px;text-align:center;font-size:13px;font-weight:700;line-height:17px}
  .nav-item svg{position:absolute;left:50%;top:28px;transform:translateX(-50%)}
  .nav-item span{position:absolute;left:0;right:0;top:80px}
  .nav-item span.two{top:72px}
  .nav-active{background:linear-gradient(var(--orange-top),var(--orange-bottom));color:var(--white)}
  .c-green{color:var(--green)} .c-blue{color:var(--blue)} .c-purple{color:var(--purple)}
  .c-amber{color:var(--amber)} .c-teal{color:var(--teal)} .c-red{color:var(--red)}
</style>
</head>
<body>
<main class="app">
  <header class="app-header">
    <div class="brand">
      <div class="brand-dot"></div>
      <div class="brand-name">AppName</div>
      <div class="brand-slogan">Here is your slogan</div>
    </div>
    <div class="welcome">Welcome back, <strong>Tom Harlow</strong></div>
    <div class="text-size"><span>A</span><span>A</span><span>A</span></div>
    <div class="search">Search
      <svg width="16" height="16" viewBox="0 0 16 16"><circle cx="6.5" cy="6.5" r="5" fill="none" stroke="#fff" stroke-width="2"/><line x1="10" y1="10" x2="15" y2="15" stroke="#fff" stroke-width="2.5"/></svg>
    </div>
    <div class="header-btn btn-help">?</div>
    <div class="header-btn btn-exit">Exit</div>
  </header>

  <aside class="sidebar">
    <div class="sidebar-title">Home Measurements</div>
    <div class="tab tab-active">
      <svg width="22" height="32" viewBox="0 0 22 32"><path d="M11 1 C7 10 1 16 1 22 a10 10 0 0 0 20 0 C21 16 15 10 11 1Z" fill="#5f6370"/><path d="M7 22 a5 5 0 0 0 5 5" stroke="#fff" stroke-width="1.6" fill="none"/></svg>
      Sugar Level
    </div>
    <div class="tab tab-pressure">
      <svg width="32" height="32" viewBox="0 0 32 32"><circle cx="16" cy="16" r="14" fill="none" stroke="#7c7f8c" stroke-width="3"/><line x1="16" y1="16" x2="22" y2="10" stroke="#7c7f8c" stroke-width="3"/><circle cx="16" cy="16" r="2.5" fill="#7c7f8c"/></svg>
      Pressure
    </div>
  </aside>

  <section class="toolbar">
    <div class="add-measure">
      <svg width="26" height="26" viewBox="0 0 26 26"><circle cx="13" cy="13" r="11.5" fill="none" stroke="#8e919c" stroke-width="2"/><path d="M13 6v14M6 13h14" stroke="#3a96d2" stroke-width="3.5"/></svg>
      Add measurement
    </div>
    <svg class="settings" width="26" height="26" viewBox="0 0 26 26"><circle cx="13" cy="13" r="11.5" fill="none" stroke="#8e919c" stroke-width="2"/><circle cx="13" cy="13" r="5.5" fill="none" stroke="#3a96d2" stroke-width="3.5" stroke-dasharray="2.6 1.7"/><circle cx="13" cy="13" r="4" fill="#3a96d2"/><circle cx="13" cy="13" r="1.8" fill="#fff"/></svg>
  </section>

  <article class="entry entry-1">
    <div class="entry-date">01/01/2013</div>
    <div class="entry-note">My Sugar Level</div>
    <div class="entry-value">6,3 mmol/l</div>
    <svg class="entry-info" width="20" height="20" viewBox="0 0 20 20"><circle cx="10" cy="10" r="9" fill="none" stroke="#2aa58a" stroke-width="1.3"/><text x="10" y="15" text-anchor="middle" font-family="Georgia,serif" font-style="italic" font-size="13" fill="#2aa58a">i</text></svg>
  </article>
  <article class="entry entry-2">
    <div class="entry-date">02/21/2013</div>
    <div class="comment-btn">Add comment</div>
    <div class="entry-value">7,9 mmol/l</div>
    <svg class="entry-info" width="20" height="20" viewBox="0 0 20 20"><circle cx="10" cy="10" r="9" fill="none" stroke="#2aa58a" stroke-width="1.3"/><text x="10" y="15" text-anchor="middle" font-family="Georgia,serif" font-style="italic" font-size="13" fill="#2aa58a">i</text></svg>
  </article>

  <nav class="bottom-nav">
    <div class="nav-item c-green">
      <svg width="32" height="34" viewBox="0 0 32 34"><rect x="4" y="1" width="10" height="22" rx="5" transform="rotate(-25 9 12)" fill="none" stroke="#6ab64c" stroke-width="2"/><rect x="16" y="10" width="10" height="22" rx="5" transform="rotate(30 21 21)" fill="#6ab64c"/></svg>
      <span>Medications</span>
    </div>
    <div class="nav-item nav-active">
      <svg width="20" height="36" viewBox="0 0 20 36"><rect x="7" y="2" width="6" height="24" rx="3" fill="none" stroke="#fff" stroke-width="2"/><circle cx="10" cy="29" r="5.5" fill="#fff"/><path d="M14 8h3M14 12h3M14 16h3" stroke="#fff" stroke-width="1.2"/></svg>
      <span class="two">Home<br>Measurements</span>
    </div>
    <div class="nav-item c-blue">
      <svg width="34" height="32" viewBox="0 0 34 32"><rect x="2" y="4" width="30" height="26" fill="none" stroke="#3a96d2" stroke-width="2.5"/><rect x="2" y="4" width="30" height="6" fill="#3a96d2"/><path d="M9 1v6M25 1v6" stroke="#3a96d2" stroke-width="3"/><text x="17" y="26" text-anchor="middle" font-family="Open Sans,Arial,sans-serif" font-weight="700" font-size="12" fill="#3a96d2">17</text></svg>
      <span>My Schedule</span>
    </div>
    <div class="nav-item c-purple">
      <svg width="34" height="34" viewBox="0 0 34 34"><rect x="2" y="2" width="30" height="22" fill="none" stroke="#7a4fb0" stroke-width="2.5"/><path d="M6 14h6l3-6 4 11 3-5h6" fill="none" stroke="#7a4fb0" stroke-width="1.8"/><path d="M12 24l-4 8M22 24l4 8" stroke="#7a4fb0" stroke-width="2.5"/></svg>
      <span>Lab Test Results</span>
    </div>
    <div class="nav-item c-amber">
      <svg width="34" height="32" viewBox="0 0 34 32"><g fill="none" stroke="#f5a638" stroke-width="2"><rect x="2" y="2" width="6" height="6"/><rect x="2" y="13" width="6" height="6"/><rect x="2" y="24" width="6" height="6"/></g><g fill="#f5a638"><rect x="13" y="3" width="20" height="4"/><rect x="13" y="14" width="20" height="4"/><rect x="13" y="25" width="20" height="4"/></g></svg>
      <span class="two">Checkups &amp;<br>Procedures</span>
    </div>
    <div class="nav-item c-teal">
      <svg width="34" height="34" viewBox="0 0 34 34"><ellipse cx="17" cy="10" rx="7" ry="9" fill="#2f9d86"/><path d="M1 34c0-9 7-14 16-14s16 5 16 14z" fill="#2f9d86"/></svg>
      <span>My Profile</span>
    </div>
    <div class="nav-item c-red">
      <svg width="34" height="30" viewBox="0 0 34 30"><path d="M17 29 C5 20 1 14 1 9 a8 8 0 0 1 16-2 a8 8 0 0 1 16 2 c0 5-4 11-16 20z" fill="#dc5248"/></svg>
      <span class="two">My Health Care<br>Providers</span>
    </div>
  </nav>
</main>
</body>
</html>
```